Real Estate Webpage Design

We have an existing website: ferndaleestatecollective.com.au
We focus customised service mainly on Property Management and second-hand property sales.
We are not entirely happy about the current design and layout can stay roughly the same as the back end coding is linked to a CRM system.
We would like to see the design are more reachable to our clients and appearing.
Please check our Website Design Draft for more details.

Industry/Entity Type

Real estate Agency

Number of Pages Required

5+ page

Font styles to use
Sans Serif

Colors

Designer to choose colors to be used in the design.

```html
<!DOCTYPE html>
<html lang="en">
<head>
<meta charset="utf-8">
<title>Ferndale Estate Collective</title>
<link href="https://fonts.googleapis.com/css2?family=Poppins:wght@400;500;600;700&family=Roboto:wght@400;500&display=swap" rel="stylesheet">
<style>
:root{
  --gold:#e9b949;
  --gold-pale:#fdf1d6;
  --navy:#263a55;
  --navy-deep:#1d3050;
  --ink:#1f2d44;
  --body:#666d78;
  --muted:#9a9fa8;
  --line:#e6e8ec;
  --cream:#fbf6ea;
  --white:#fff;
}
*{box-sizing:border-box;margin:0;padding:0}
html,body{width:1200px;height:4419px;overflow:hidden}
body{font-family:"Roboto",sans-serif;color:var(--body);background:var(--white);position:relative}
h1,h2,h3,h4,.brand,.btn{font-family:"Poppins",sans-serif}
.icon{width:14px;height:14px;fill:currentColor;flex:none}
.sec{position:absolute;left:0;width:1200px}

/* nav */
.nav{top:0;height:86px;display:flex;align-items:center;padding:0 86px;white-space:nowrap}
.brand{display:flex;align-items:center;gap:10px;font-weight:600;font-size:30px;color:var(--ink);line-height:1}
.brand-mark{width:36px;height:36px;border:3px solid var(--gold);border-radius:4px}
.brand small{display:block;font-size:10px;font-weight:400;color:var(--ink);margin-top:3px}
.menu{display:flex;gap:22px;margin-left:26px;font-size:14px;color:var(--ink);font-family:"Poppins",sans-serif;white-space:nowrap}
.menu span{white-space:nowrap}
.menu span.dd::after{content:"";display:inline-block;width:5px;height:5px;border-right:1.5px solid var(--ink);border-bottom:1.5px solid var(--ink);transform:rotate(45deg);margin:0 0 3px 5px}
.add-btn{margin-left:auto;display:flex;align-items:center;gap:12px;background:var(--gold);color:#fff;font-family:"Poppins",sans-serif;font-size:13px;font-weight:500;height:42px;padding:0 20px 0 8px;border-radius:22px;white-space:nowrap}
.add-btn i{width:28px;height:28px;border-radius:50%;background:#fff;position:relative}
.add-btn i::before,.add-btn i::after{content:"";position:absolute;background:var(--gold);left:13px;top:8px;width:2px;height:12px}
.add-btn i::after{transform:rotate(90deg)}
.user{margin-left:12px;width:42px;height:42px;border-radius:50%;background:var(--gold);display:flex;align-items:center;justify-content:center;color:#fff}

/* hero */
.hero{top:86px;height:586px}
.hero-photo{position:absolute;inset:0;background:linear-gradient(90deg,#f5f5f4 0%,#eeeeed 48%,#d6d7d8 66%,#b4b6b8 82%,#8d9094 100%)}
.hero-card{position:absolute;left:86px;top:132px;width:554px;height:382px;background:#fff;border-radius:8px;box-shadow:0 10px 30px rgba(0,0,0,.08);padding:78px 42px 0}
.hero-card h1{font-size:31px;line-height:38px;font-weight:600;color:var(--ink)}
.tabs{display:flex;gap:12px;margin-top:24px}
.tab{height:42px;padding:0 22px;display:flex;align-items:center;background:#fbf1d8;color:var(--ink);font-family:"Poppins",sans-serif;font-weight:500;font-size:16px;border-radius:4px 4px 0 0}
.tab.on{background:var(--gold);color:#fff;padding:0 30px}
.search{height:62px;border:1px solid var(--line);box-shadow:0 4px 12px rgba(0,0,0,.05);display:flex;align-items:center;font-size:12px;color:var(--muted);padding:0 22px;width:458px}
.search .loc{margin-left:auto;width:210px;border-left:1px solid var(--line);padding-left:16px;display:flex;justify-content:space-between}
.search .loc b{color:var(--gold);font-size:11px}
.btn{display:inline-flex;align-items:center;justify-content:center;background:var(--gold);color:#fff;font-weight:500;border-radius:4px;white-space:nowrap}
.hero-card .btn{margin-top:20px;height:46px;width:120px;font-size:12px;font-weight:600}

/* about */
.about{top:672px;height:699px}
.eyebrow{font-family:"Poppins",sans-serif;font-size:12px;font-weight:600;color:var(--gold);letter-spacing:.5px;text-transform:uppercase}
.about-text{position:absolute;left:86px;top:162px;width:520px}
.about-text h2{font-size:30px;line-height:38px;color:var(--ink);font-weight:600;margin-top:8px}
.tagline{display:flex;align-items:center;gap:12px;color:var(--gold);font-family:"Poppins",sans-serif;font-size:17px;margin:22px 0 16px}
.tagline::before{content:"";width:40px;height:1px;background:var(--gold)}
.about-text p{font-size:13px;line-height:21px;margin-bottom:14px}
.about-text .btn{height:50px;width:188px;font-size:15px;margin-top:10px}
.ph{position:absolute;border-radius:6px}
.ph-1{left:837px;top:113px;width:363px;height:205px;background:linear-gradient(160deg,#f2f1ee 0%,#e4e1db 50%,#d2b893 85%,#b98a5e 100%)}
.ph-2{left:675px;top:345px;width:260px;height:243px;background:linear-gradient(180deg,#f4f3f1 0%,#e8e6e2 50%,#c9c3b9 80%,#a9b09a 100%)}
.ph-3{left:958px;top:345px;width:242px;height:243px;background:linear-gradient(180deg,#f5f5f4 0%,#ebe9e6 55%,#e2d9c7 100%)}
.dots{position:absolute;left:722px;top:232px;width:130px;height:100px;background-image:radial-gradient(#5a6270 1.2px,transparent 1.4px);background-size:15px 15px}

/* properties */
.props{top:1371px;height:786px;background:var(--navy)}
.center-head{text-align:center}
.center-head h2{font-size:29px;font-weight:600;margin-top:6px}
.props .center-head{padding-top:110px;color:#fff}
.props .eyebrow{color:#fff}
.ptabs{position:absolute;left:173px;top:188px;width:852px;height:50px;background:#fff;border-radius:4px;display:flex;align-items:center;font-family:"Poppins",sans-serif;font-size:15px;color:var(--gold)}
.ptabs span{flex:1;text-align:center;border-left:1px solid var(--line)}
.ptabs span.on{background:var(--gold);color:#fff;height:50px;line-height:50px;border-radius:4px 0 0 4px;border:none;flex:0 0 162px}
.ptabs span.on+span{border-left:none}
.cards{position:absolute;left:88px;top:268px;display:flex;gap:26px}
.pcard{width:325px;height:405px;background:#fff;border-radius:3px;overflow:hidden}
.pimg{height:208px;padding:152px 0 0 32px;color:#fff;font-family:"Poppins",sans-serif;font-weight:600;font-size:20px;text-shadow:0 1px 4px rgba(0,0,0,.35)}
.pimg-1{background:linear-gradient(180deg,#8db4e2 0%,#b9c6cf 35%,#d9d6cf 55%,#8c8a86 80%,#5b5d62 100%)}
.pimg-2{background:linear-gradient(90deg,#dfe2e5 0%,#f1f1f0 40%,#cfd1d3 70%,#6f7276 100%)}
.pimg-3{background:linear-gradient(180deg,#9ec0e6 0%,#7f9a6e 30%,#5f7a4c 65%,#a9a69c 100%)}
.suburb{display:inline-block;margin-left:32px;background:var(--gold-pale);color:var(--gold);font-size:13px;padding:4px 24px;font-family:"Poppins",sans-serif}
.pcard h3{font-size:18px;color:var(--ink);font-weight:600;margin:14px 0 14px 24px}
.meta{margin-left:24px;font-size:13px;color:var(--body);display:flex;align-items:center;gap:10px;margin-bottom:10px}
.meta .icon{color:var(--muted)}
.feats{display:flex;gap:12px;margin:28px 0 0 24px;font-size:13px;color:var(--ink);align-items:center}
.feats span{display:flex;align-items:center;gap:8px}
.feats .icon{color:var(--gold);width:18px;height:16px}

/* team */
.team{top:2157px;height:728px}
.team .center-head{padding-top:118px;color:var(--ink)}
.tcards{position:absolute;left:86px;top:198px;display:flex;gap:26px;align-items:flex-start}
.tcard{width:325px;height:325px;background:#f7f8fa;text-align:center;padding-top:26px}
.tcard.tall{height:365px;background:#fff;box-shadow:0 6px 24px rgba(0,0,0,.07)}
.avatar{width:128px;height:128px;border-radius:50%;background:linear-gradient(180deg,#eef0f2 0%,#e3e5e8 55%,#2c3444 100%);margin:0 auto}
.tcard h3{font-size:19px;color:var(--ink);font-weight:600;margin-top:18px;white-space:nowrap}
.tcard h3 small{font-size:12px;color:var(--muted);font-weight:400;font-family:"Roboto",sans-serif}
.role{font-size:12px;color:var(--muted);line-height:15px;margin-top:2px}
.pills{display:flex;gap:12px;justify-content:center;margin-top:12px}
.pill{display:inline-flex;align-items:center;gap:8px;background:var(--gold);color:var(--ink);font-size:12px;height:32px;padding:0 16px;border-radius:16px;white-space:nowrap}
.mail{display:inline-flex;align-items:center;gap:8px;background:#fff;border:1px solid var(--line);font-size:11.5px;color:var(--ink);height:32px;padding:0 14px;border-radius:16px;margin-top:12px;white-space:nowrap}
.pager{position:absolute;top:600px;left:0;width:1200px;display:flex;justify-content:center;align-items:center;gap:12px}
.pager i{width:8px;height:8px;border-radius:50%;background:#b8bcc4}
.pager i.on{width:18px;height:18px;background:var(--navy)}

/* testimonials */
.testi{top:2885px;height:412px;background:var(--cream)}
.testi .center-head{padding-top:118px;color:var(--ink)}
.quote{position:absolute;left:0;top:228px;width:1200px;text-align:center;color:var(--ink);font-size:15px;line-height:22px}
.quote b{display:block;font-family:"Poppins",sans-serif;font-weight:600;font-size:19px;margin-top:14px}
.arrow{position:absolute;top:240px;width:54px;height:54px;border-radius:50%;background:#fff;box-shadow:0 3px 12px rgba(0,0,0,.08);display:flex;align-items:center;justify-content:center;color:var(--ink)}

/* blog */
.blog{top:3297px;height:685px}
.blog-head{position:absolute;left:86px;top:118px;color:var(--ink)}
.blog-head h2{font-size:29px;font-weight:600;margin-top:4px}
.view-all{position:absolute;right:86px;top:116px;height:50px;width:188px;font-size:15px}
.bcards{position:absolute;left:86px;top:192px;display:flex;gap:26px}
.bcard{width:325px;height:385px;background:#fff;box-shadow:0 6px 24px rgba(0,0,0,.07);padding:20px 24px}
.bimg{height:174px;position:relative}
.bimg-1{background:linear-gradient(90deg,#d9dbdc 0%,#f2f3f3 35%,#e6e8e9 65%,#c7cdd1 100%)}
.bimg-2{background:linear-gradient(180deg,#6f9fde 0%,#b9d0ea 40%,#cfd6dc 60%,#9aa3ab 100%)}
.bimg-3{background:linear-gradient(160deg,#eef0f2 0%,#e3ddd3 50%,#c79b6f 80%,#8b7a66 100%)}
.date{position:absolute;left:8px;bottom:-10px;width:56px;height:54px;background:var(--gold);color:#fff;text-align:center;font-family:"Poppins",sans-serif;font-weight:600;font-size:18px;line-height:20px;padding-top:7px;border-radius:3px}
.date small{display:block;font-size:12px;font-weight:500}
.bmeta{font-size:12px;color:var(--body);margin-top:28px;display:flex;gap:16px}
.bmeta span::before{content:"";display:inline-block;width:6px;height:6px;border-radius:50%;background:var(--muted);margin-right:8px}
.bcard h3{font-size:18px;line-height:26px;color:var(--ink);font-weight:600;margin-top:8px}
.more{color:var(--gold);font-size:13px;margin-top:12px;display:flex;align-items:center;gap:8px}
.more::after{content:"";width:22px;height:1px;background:var(--gold)}

/* footer */
.foot{top:3982px;height:364px;background:linear-gradient(180deg,var(--navy-deep),#1c3355);color:#fff}
.foot .brand{position:absolute;left:86px;top:58px;color:#fff}
.foot .brand small{color:#fff}
.about-foot{position:absolute;left:86px;top:126px;width:330px;font-size:13px;line-height:21px}
.social{position:absolute;left:92px;top:244px;display:flex;gap:14px}
.social i{width:36px;height:36px;border:1px solid rgba(255,255,255,.4);display:block}
.fcol{position:absolute;top:60px}
.fcol h4{font-size:19px;font-weight:500;margin-bottom:28px;white-space:nowrap}
.fcol li{list-style:none;font-size:13px;line-height:18px;margin-bottom:16px;position:relative;padding-left:22px;white-space:nowrap}
.fcol li::before{content:"";position:absolute;left:2px;top:5px;width:7px;height:7px;border-radius:50%;background:var(--gold)}
.news input{display:block;width:202px;height:38px;border:none;padding:0 18px;font-size:12px;font-family:"Roboto",sans-serif;margin-top:2px}
.news .btn{margin-top:12px;width:106px;height:38px;font-size:12px}
.contact p{display:flex;gap:12px;font-size:13px;line-height:18px;margin-bottom:22px;white-space:nowrap}
.contact .icon{color:var(--gold);margin-top:2px}
.copy{top:4346px;height:73px;background:#16243c;color:#fff;font-size:13px;display:flex;align-items:center;justify-content:center}
</style>
</head>
<body>
<svg width="0" height="0" style="position:absolute" aria-hidden="true">
  <symbol id="i-phone" viewBox="0 0 24 24"><path d="M6.6 10.8a15 15 0 0 0 6.6 6.6l2.2-2.2c.3-.3.7-.4 1-.2 1.1.4 2.3.6 3.6.6.6 0 1 .4 1 1V20c0 .6-.4 1-1 1A17 17 0 0 1 3 4c0-.6.4-1 1-1h3.5c.6 0 1 .4 1 1 0 1.3.2 2.5.6 3.6.1.3 0 .7-.2 1z"/></symbol>
  <symbol id="i-mobile" viewBox="0 0 24 24"><path d="M7 2h10a2 2 0 0 1 2 2v16a2 2 0 0 1-2 2H7a2 2 0 0 1-2-2V4a2 2 0 0 1 2-2zm0 3v13h10V5z"/></symbol>
  <symbol id="i-mail" viewBox="0 0 24 24"><path d="M3 5h18v14H3zm2 2v.5l7 4.5 7-4.5V7zm0 3v7h14v-7l-7 4.5z"/></symbol>
  <symbol id="i-star" viewBox="0 0 24 24"><path d="M12 2l3 7 7 .6-5.3 4.6 1.6 7.3L12 17.8 5.7 21.5l1.6-7.3L2 9.6 9 9z"/></symbol>
  <symbol id="i-pin" viewBox="0 0 24 24"><path d="M12 2a7 7 0 0 0-7 7c0 5 7 13 7 13s7-8 7-13a7 7 0 0 0-7-7zm0 9.5a2.5 2.5 0 1 1 0-5 2.5 2.5 0 0 1 0 5z"/></symbol>
  <symbol id="i-bed" viewBox="0 0 24 20"><path d="M2 3h2v8h16V6h2v12h-2v-3H4v3H2zm4 2h5v5H6zm7 1h6v4h-6z"/></symbol>
  <symbol id="i-bath" viewBox="0 0 24 20"><path d="M5 2h4l2 3-1 1-2-2H7v8h15v2a5 5 0 0 1-3 4l1 2h-2l-1-1H7l-1 1H4l1-2a5 5 0 0 1-3-4v-2h3z"/></symbol>
  <symbol id="i-car" viewBox="0 0 24 20"><path d="M5 6l2-4h10l2 4h2v3h-1v7h-3v-2H7v2H4V9H3V6zm3-2-1 3h10l-1-3zm-2 6v2h3v-2zm9 0v2h3v-2z"/></symbol>
  <symbol id="i-user" viewBox="0 0 24 24"><path d="M12 12a5 5 0 1 0 0-10 5 5 0 0 0 0 10zm0 2c-5 0-9 2.5-9 6v2h18v-2c0-3.5-4-6-9-6z"/></symbol>
  <symbol id="i-fax" viewBox="0 0 24 24"><path d="M6 2h9l3 3v4h2a2 2 0 0 1 2 2v9H2v-9a2 2 0 0 1 2-2h2zm2 2v5h8V6h-2V4zm0 9v2h2v-2zm4 0v2h2v-2zm4 0v2h2v-2z"/></symbol>
  <symbol id="i-left" viewBox="0 0 24 24"><path d="M15 5l-7 7 7 7" fill="none" stroke="currentColor" stroke-width="2"/></symbol>
  <symbol id="i-right" viewBox="0 0 24 24"><path d="M9 5l7 7-7 7" fill="none" stroke="currentColor" stroke-width="2"/></symbol>
</svg>

<header class="sec nav">
  <div class="brand"><span class="brand-mark"></span><div>Ferndale<small>Property Group</small></div></div>
  <nav class="menu"><span>Home</span><span>About us</span><span class="dd">Leasing</span><span>Buy</span><span class="dd">Sell</span><span>Our Team</span><span>Blog</span><span>Contact Us</span></nav>
  <div class="add-btn"><i></i>Add Property</div>
  <div class="user"><svg class="icon" style="width:20px;height:20px"><use href="#i-user"/></svg></div>
</header>

<section class="sec hero">
  <div class="hero-photo" role="img" aria-label="Bright modern kitchen interior with grey cabinetry"></div>
  <div class="hero-card">
    <h1>Ferndale – Property Group<br>Your place called “the home”</h1>
    <div class="tabs"><span class="tab on">Sell</span><span class="tab">Buy</span><span class="tab">Lease</span></div>
    <div class="search"><span>Enter keyword here...</span><span class="loc">Select location <b>▼</b></span></div>
    <span class="btn">SEARCH</span>
  </div>
</section>

<section class="sec about">
  <div class="about-text">
    <div class="eyebrow">About us</div>
    <h2>Welcome to Ferndale Estate Collective</h2>
    <div class="tagline">Your local real estate property group</div>
    <p>Ferndale stands for “the home, the house”: buying a property is one of the most expensive expenses and important assets for people. Ferndale is a real estate company located in Gungahlin, Canberra.</p>
    <p>Being a portfolio sales agent and property manager, coupled with our high-profile international real estate experience, Ferndale is considered a market leader on the cutting edge with deep industry knowledge, ranging from landlord–tenant relationships, residential purchases.</p>
    <span class="btn">Contact With Us</span>
  </div>
  <div class="dots" aria-hidden="true"></div>
  <div class="ph ph-1" role="img" aria-label="Study nook with timber desk and window"></div>
  <div class="ph ph-2" role="img" aria-label="Living room with grey sofa and plant"></div>
  <div class="ph ph-3" role="img" aria-label="Bright bedroom with white linen"></div>
</section>

<section class="sec props">
  <div class="center-head"><div class="eyebrow">Our properties</div><h2>This Month At Ferndale Estate Collective</h2></div>
  <div class="ptabs"><span class="on">For Lease</span><span>For Sale</span><span>Open Times</span><span>Sold</span><span>Leased</span></div>
  <div class="cards">
    <article class="pcard">
      <div class="pimg pimg-1" role="img" aria-label="Two-storey house with double garage">$1400 pw</div>
      <span class="suburb">Red Hill</span>
      <h3>9 Banksia Street Red Hill</h3>
      <div class="meta"><svg class="icon"><use href="#i-star"/></svg>Add to favourites</div>
      <div class="meta"><svg class="icon"><use href="#i-mail"/></svg>Email to agents</div>
      <div class="feats"><span><svg class="icon"><use href="#i-bed"/></svg>Beds 4</span><span><svg class="icon"><use href="#i-bath"/></svg>Baths 2</span><span><svg class="icon"><use href="#i-car"/></svg>Parking 2</span></div>
    </article>
    <article class="pcard">
      <div class="pimg pimg-2" role="img" aria-label="Apartment living room with city view">$560 pw</div>
      <span class="suburb">Braddon</span>
      <h3>215/2 Acacia Street Braddon</h3>
      <div class="meta"><svg class="icon"><use href="#i-star"/></svg>Add to favourites</div>
      <div class="meta"><svg class="icon"><use href="#i-mail"/></svg>Email to agents</div>
      <div class="feats"><span><svg class="icon"><use href="#i-bed"/></svg>Beds 1</span><span><svg class="icon"><use href="#i-bath"/></svg>Baths 1</span><span><svg class="icon"><use href="#i-car"/></svg>Parking 1</span></div>
    </article>
    <article class="pcard">
      <div class="pimg pimg-3" role="img" aria-label="Front garden with hedges and entry path">$1300 pw</div>
      <span class="suburb">Griffith</span>
      <h3>1 Myrtle Street Griffith</h3>
      <div class="meta"><svg class="icon"><use href="#i-star"/></svg>Add to favourites</div>
      <div class="meta"><svg class="icon"><use href="#i-mail"/></svg>Email to agents</div>
      <div class="feats"><span><svg class="icon"><use href="#i-bed"/></svg>Beds 4</span><span><svg class="icon"><use href="#i-bath"/></svg>Baths 2</span><span><svg class="icon"><use href="#i-car"/></svg>Parking 3</span></div>
    </article>
  </div>
</section>

<section class="sec team">
  <div class="center-head"><div class="eyebrow">Our team</div><h2>Our Exclusive Team</h2></div>
  <div class="tcards">
    <div class="tcard">
      <div class="avatar" role="img" aria-label="Portrait photo of the principal"></div>
      <h3>Wei Lin <small>Principal</small></h3>
      <div class="pills"><span class="pill"><svg class="icon"><use href="#i-phone"/></svg>+61 6200 1234</span><span class="pill"><svg class="icon"><use href="#i-mobile"/></svg>0400 111 222</span></div>
      <span class="mail"><svg class="icon"><use href="#i-mail"/></svg>wlin@ferndaleestatecollective.com.au</span>
    </div>
    <div class="tcard tall">
      <div class="avatar" role="img" aria-label="Portrait photo of the senior property manager"></div>
      <h3>Marta Chen</h3>
      <div class="role">Business Relationship Manager &amp; Senior<br>Property Manager</div>
      <div class="pills"><span class="pill"><svg class="icon"><use href="#i-phone"/></svg>+61 6200 1234</span><span class="pill"><svg class="icon"><use href="#i-mobile"/></svg>0400 333 444</span></div>
      <span class="mail"><svg class="icon"><use href="#i-mail"/></svg>marta.chen@ferndaleestatecollective.com.au</span>
    </div>
    <div class="tcard">
      <div class="avatar" role="img" aria-label="Portrait photo of the property manager"></div>
      <h3>Nadia Park <small>Property Manager</small></h3>
      <div class="pills"><span class="pill"><svg class="icon"><use href="#i-phone"/></svg>+61 6200 1234</span><span class="pill"><svg class="icon"><use href="#i-mobile"/></svg>0400 555 666</span></div>
      <span class="mail"><svg class="icon"><use href="#i-mail"/></svg>inspect@ferndaleestatecollective.com.au</span>
    </div>
  </div>
  <div class="pager"><i></i><i class="on"></i><i></i><i></i></div>
</section>

<section class="sec testi">
  <div class="center-head"><div class="eyebrow">Testimonials</div><h2>What’s Our Customer Say</h2></div>
  <span class="arrow" style="left:86px"><svg class="icon" style="width:18px;height:18px"><use href="#i-left"/></svg></span>
  <span class="arrow" style="right:86px"><svg class="icon" style="width:18px;height:18px"><use href="#i-right"/></svg></span>
  <p class="quote">Nadia is my best property manager! Always happy to response my queries and keep us well informed<br>at all stage.&nbsp; I will definitely recommend her to my friends.<b>- li hua</b></p>
</section>

<section class="sec blog">
  <div class="blog-head"><div class="eyebrow">What’s new trending</div><h2>Latest Blog &amp; Posts</h2></div>
  <span class="btn view-all">View All Posts</span>
  <div class="bcards">
    <article class="bcard"><div class="bimg bimg-1" role="img" aria-label="Empty apartment room with large windows"><span class="date">13<small>May</small></span></div><div class="bmeta"><span>Real Estate</span><span>1 Min</span></div><h3>Lorem Ipsum is simply dummy text of the printing</h3><div class="more">Read More</div></article>
    <article class="bcard"><div class="bimg bimg-2" role="img" aria-label="Balcony chairs overlooking a lake"><span class="date">13<small>May</small></span></div><div class="bmeta"><span>Real Estate</span><span>1 Min</span></div><h3>Lorem Ipsum is simply dummy text of the printing</h3><div class="more">Read More</div></article>
    <article class="bcard"><div class="bimg bimg-3" role="img" aria-label="Open-plan living area with city views"><span class="date">13<small>May</small></span></div><div class="bmeta"><span>Real Estate</span><span>1 Min</span></div><h3>Lorem Ipsum is simply dummy text of the printing</h3><div class="more">Read More</div></article>
  </div>
</section>

<footer class="sec foot">
  <div class="brand"><span class="brand-mark"></span><div>Ferndale<small>Property Group</small></div></div>
  <p class="about-foot">Ferndale Estate Collective aims to at all times maintain the utmost levels of service for our customers and strives to place itself at the forefront of Property Management Services within the Real Estate industry.</p>
  <div class="social"><i aria-label="Social link"></i><i aria-label="Social link"></i><i aria-label="Social link"></i></div>
  <div class="fcol" style="left:460px"><h4>Quick Links</h4><ul><li>Contact Us</li><li>Privacy</li><li>Complaint Handling &amp;<br>Dispute Resolution</li><li>Due Diligence Checklist</li><li>Sitemap</li></ul></div>
  <div class="fcol news" style="left:684px"><h4>Newsletter</h4><input type="text" placeholder="Enter Email" aria-label="Email"><span class="btn">Subscribe</span></div>
  <div class="fcol contact" style="left:933px"><h4>Get In Touch</h4>
    <p><svg class="icon"><use href="#i-pin"/></svg>18/4 Wattle Grove Ave,<br>Gungahlin, ACT, 2912</p>
    <p><svg class="icon"><use href="#i-phone"/></svg>02 6200 1234</p>
    <p><svg class="icon"><use href="#i-fax"/></svg>02 6200 5678</p>
  </div>
</footer>
<div class="sec copy">Copyright 2022 Ferndale. All right Reserved.</div>
</body>
</html>
```